Communication and Marketing agency needs a new presentation card

We are a group of communication and marketing agencies specialized in companies that are in the logistics and industrial sector. The head agency is TELVANO Grupo and the group consists of 4 agencies: TELVANO Media, TELVANO Digital, TELVANO Research and DifundeEnPantalla. We hace 4 offices in Spain (Madrid, Barcelona, Valencia and Murcia). We are looking for a clean and attractive design that transmits our experience, brand presence in the market and knowledge to those who receive the card.It has to maintain the colors of the logo that is attached.
Target Market(s)
logistics and industrial sector
Marketing department
Contact Information for Business Card
Clean and attractive design

```html
<!DOCTYPE html>
<html lang="en">
<head>
<meta charset="utf-8">
<title>TELVANO Grupo – Business Card</title>
<link href="https://fonts.googleapis.com/css2?family=Nunito+Sans:wght@300;400;600;700&display=swap" rel="stylesheet">
<style>
  :root{
    --bg:#e4e4e4;
    --card-white:#f4f4f4;
    --brand-red:#a8161e;
    --brand-red-light:#b9353c;
    --slate:#4f5052;
    --charcoal:#3d3e40;
    --ink:#1d1d1f;
    --muted:#c9c9c9;
    --white:#ffffff;
  }
  *{margin:0;padding:0;box-sizing:border-box}
  html,body{width:1200px;height:960px;overflow:hidden}
  body{background:var(--bg);font-family:"Nunito Sans",sans-serif;position:relative}

  .card{position:absolute;width:540px;height:320px;border-radius:4px;overflow:hidden;box-shadow:0 6px 18px rgba(0,0,0,.12)}
  .card--front{left:40px;top:320px;background:var(--card-white)}
  .card--back{left:620px;top:320px;background:var(--charcoal);display:flex;align-items:center;justify-content:center}

  .identity{position:absolute;left:36px;top:40px}
  .identity__name{font-size:24px;font-weight:400;color:var(--ink);letter-spacing:.5px;line-height:1}
  .identity__position{font-size:15px;font-weight:400;color:var(--brand-red);margin-top:4px;letter-spacing:.5px}
  .identity__rule{width:30px;height:1px;background:var(--muted);margin-top:8px}

  .contact{position:absolute;left:36px;top:128px;list-style:none}
  .contact__item{display:flex;align-items:center;gap:12px;font-size:14px;color:var(--ink);height:24px;margin-bottom:6px}
  .contact__icon{width:20px;height:20px;flex:none}

  .logo{position:absolute;right:36px;top:88px;text-align:right}
  .logo__main{font-size:38px;font-weight:400;color:var(--brand-red);letter-spacing:1px;line-height:1}
  .logo__main span{display:block;font-size:22px;color:var(--ink)}

  .subbrands{position:absolute;right:36px;top:160px;display:flex;gap:18px;align-items:flex-start}
  .subbrand{display:flex;flex-direction:column;align-items:flex-end;line-height:1.1}
  .subbrand__name{font-size:10px;font-weight:600;color:var(--slate);letter-spacing:.3px}
  .subbrand__unit{font-size:9px;font-weight:600;color:var(--brand-red)}
  .subbrand--digital{margin-top:10px}
  .subbrand--media{margin-top:20px}

  .follow{position:absolute;left:0;top:236px;width:236px;height:44px;background:var(--slate);border-radius:0 12px 12px 0;display:flex;align-items:center;padding-left:26px;color:var(--muted);font-size:14px;font-weight:300}
  .social{position:absolute;left:250px;bottom:0;width:290px;height:62px;background:linear-gradient(90deg,var(--brand-red),var(--brand-red-light));border-radius:14px 0 0 0;display:flex;align-items:center;justify-content:space-evenly;padding:0 10px}
  .social__name{color:var(--white);font-size:12px;font-weight:700;letter-spacing:.3px}

  .back-logo{font-size:48px;font-weight:400;color:var(--brand-red);letter-spacing:1px;text-align:right;line-height:1}
  .back-logo span{display:block;font-size:26px}
</style>
</head>
<body>
  <section class="card card--front" aria-label="Business card front">
    <div class="identity">
      <p class="identity__name">YOUR NAME</p>
      <p class="identity__position">POSITION</p>
      <div class="identity__rule"></div>
    </div>

    <ul class="contact">
      <li class="contact__item">
        <svg class="contact__icon" viewBox="0 0 20 20" aria-hidden="true"><circle cx="10" cy="10" r="10" fill="#a8161e"/><path d="M7 5.5c.6-.3 1.2 0 1.4.6l.5 1.4c.2.5 0 .9-.4 1.2l-.6.4c.5 1.2 1.4 2.1 2.6 2.6l.4-.6c.3-.4.7-.6 1.2-.4l1.4.5c.6.2.9.8.6 1.4-.5 1.1-1.6 1.6-2.7 1.2C8.7 12.8 7.2 11.3 6.2 8.6 5.8 7.1 6 6 7 5.5z" fill="#fff"/></svg>
        +00 0000 000 000
      </li>
      <li class="contact__item">
        <svg class="contact__icon" viewBox="0 0 20 20" aria-hidden="true"><circle cx="10" cy="10" r="10" fill="#a8161e"/><rect x="5" y="6.5" width="10" height="7" fill="none" stroke="#fff" stroke-width="1.2"/><path d="M5 6.5l5 4 5-4" fill="none" stroke="#fff" stroke-width="1.2"/></svg>
        info@telvanogrupo.com
      </li>
      <li class="contact__item">
        <svg class="contact__icon" viewBox="0 0 20 20" aria-hidden="true"><circle cx="10" cy="10" r="10" fill="#a8161e"/><path d="M10 4.5a3.6 3.6 0 0 0-3.6 3.6c0 2.6 3.6 7 3.6 7s3.6-4.4 3.6-7A3.6 3.6 0 0 0 10 4.5z" fill="#fff"/><circle cx="10" cy="8.1" r="1.4" fill="#a8161e"/></svg>
        Office Address
      </li>
    </ul>

    <div class="logo">
      <p class="logo__main">TELVANO <span>Grupo</span></p>
    </div>

    <div class="subbrands">
      <div class="subbrand subbrand--research"><span class="subbrand__name">TELVANO</span><span class="subbrand__unit">Research</span></div>
      <div class="subbrand subbrand--digital"><span class="subbrand__name">TELVANO</span><span class="subbrand__unit">Digital</span></div>
      <div class="subbrand subbrand--media"><span class="subbrand__name">TELVANO</span><span class="subbrand__unit">Media</span></div>
    </div>

    <div class="follow">Follow us @telvanogrupo</div>
    <div class="social">
      <span class="social__name">Plazo</span>
      <span class="social__name">Lumo</span>
      <span class="social__name">Pio</span>
      <span class="social__name">Redna</span>
      <span class="social__name">Fanto</span>
    </div>
  </section>

  <section class="card card--back" aria-label="Business card back">
    <p class="back-logo">TELVANO <span>Grupo</span></p>
  </section>
</body>
</html>
```